Salon and Spa Distributor Business Card

Need a business card. We are are distributor in the salon and spa industry. We identify with natural beauty. Need a card with:
Company Name: Petal Quarry"
Title: "President & CEO"
Address
Company Phone number
email
website
Tag Line:" Natural Supply for Salon Pros"

Industry/Entity Type

Business

Contact Information for Business Card

Name: Dov Strommen
Title: "President & CEO"
Address: 31 Harlow Ln, Bexmoor, NJ 07813
Company Phone number: 800-463-5918
email: dovstrommen@petalquarry.example
website: www.petalquarry.example

Requirements
Should not have
• No black backgrounds

```html
<!DOCTYPE html>
<html lang="en">
<head>
<meta charset="utf-8">
<title>Petal Quarry – Business Card</title>
<link rel="stylesheet" href="https://fonts.googleapis.com/css2?family=Mulish:wght@300;400;700&display=swap">
<style>
  :root {
    --bg: #efefef;
    --paper: #f7f7f6;
    --green: #3f9a2e;
    --green-dark: #3a8533;
    --green-light: #57ab37;
    --ink-grey: #7d7d7d;
    --ink-dark: #5e5e5e;
    --white: #ffffff;
  }
  * { box-sizing: border-box; margin: 0; padding: 0; }
  html, body {
    width: 1200px; height: 900px; overflow: hidden;
    background: var(--bg);
    font-family: "Mulish", Arial, sans-serif;
  }
  .canvas {
    position: relative; width: 1200px; height: 900px;
    display: flex; align-items: center; justify-content: center; gap: 40px;
  }
  .card {
    position: relative; width: 540px; height: 309px; overflow: hidden;
    box-shadow: 0 6px 18px rgba(0,0,0,0.10);
  }
  .card--front { background: var(--paper); }
  .card--back {
    background: linear-gradient(135deg, var(--green-dark) 0%, var(--green-light) 100%);
    display: flex; flex-direction: column; align-items: center; justify-content: center;
  }

  .brand { display: flex; align-items: center; gap: 12px; }
  .brand__dot { width: 30px; height: 30px; border-radius: 50%; flex: none; }
  .brand__name { font-weight: 300; letter-spacing: 0.5px; white-space: nowrap; }

  .card--front .brand { position: absolute; left: 44px; top: 62px; }
  .card--front .brand__dot { background: var(--green); }
  .card--front .brand__name { color: var(--green); font-size: 26px; }

  .card--back .brand__dot { background: var(--white); width: 40px; height: 40px; }
  .card--back .brand__name { color: var(--white); font-size: 38px; }
  .tagline {
    color: var(--white); font-size: 15px; font-weight: 400;
    letter-spacing: 0.6px; margin-top: 8px; margin-left: 52px; white-space: nowrap;
  }

  .contact {
    position: absolute; left: 250px; top: 112px; width: 260px;
    color: var(--ink-grey); font-size: 13px; line-height: 1.4;
  }
  .contact__name { color: var(--green); font-weight: 700; font-size: 20px; line-height: 1.15; }
  .contact__title { font-size: 16px; color: var(--ink-grey); line-height: 1.25; margin-top: 1px; }
  .contact__rule { border: 0; border-top: 1px solid var(--green-light); margin: 6px 0 7px; }
  .contact__company { font-weight: 700; color: var(--ink-dark); }
  .contact__row { display: flex; align-items: center; gap: 7px; white-space: nowrap; }
  .contact__row svg { width: 11px; height: 11px; fill: var(--green); flex: none; }
  .contact__address { margin-bottom: 4px; }
</style>
</head>
<body>
<main class="canvas">
  <section class="card card--front" aria-label="Business card front">
    <div class="brand">
      <span class="brand__dot"></span>
      <span class="brand__name">Petal Quarry</span>
    </div>
    <div class="contact">
      <p class="contact__name">Dov Strommen</p>
      <p class="contact__title">President &amp; CEO</p>
      <hr class="contact__rule">
      <p class="contact__address"><span class="contact__company">Petal Quarry</span>, 31 Harlow Ln<br>Bexmoor, NJ 07813</p>
      <p class="contact__row">
        <svg viewBox="0 0 24 24" aria-hidden="true"><path d="M6.6 10.8a15 15 0 0 0 6.6 6.6l2.2-2.2a1 1 0 0 1 1-.25 11.4 11.4 0 0 0 3.6.57 1 1 0 0 1 1 1V20a1 1 0 0 1-1 1A17 17 0 0 1 3 4a1 1 0 0 1 1-1h3.5a1 1 0 0 1 1 1c0 1.25.2 2.45.57 3.57a1 1 0 0 1-.25 1z"/></svg>
        800 463 5918
      </p>
      <p class="contact__row">
        <svg viewBox="0 0 24 24" aria-hidden="true"><path d="M2 5h20v14H2z M2 5l10 8 10-8" fill="none" stroke="#3f9a2e" stroke-width="2.4"/></svg>
        dovstrommen@petalquarry.example
      </p>
      <p class="contact__row">
        <svg viewBox="0 0 24 24" aria-hidden="true"><circle cx="12" cy="12" r="9.5" fill="none" stroke="#3f9a2e" stroke-width="2.2"/><path d="M2.5 12h19M12 2.5c3 3 3 16 0 19M12 2.5c-3 3-3 16 0 19" fill="none" stroke="#3f9a2e" stroke-width="1.8"/></svg>
        www.petalquarry.example
      </p>
    </div>
  </section>

  <section class="card card--back" aria-label="Business card back">
    <div class="brand">
      <span class="brand__dot"></span>
      <span class="brand__name">Petal Quarry</span>
    </div>
    <p class="tagline">Natural Supply for Salon Pros</p>
  </section>
</main>
</body>
</html>
```